A private security company called "Tavron Security Services Ltd"

Hello everybody,

We need a web page for a company based in NZ. It is mainly an informative website so it would be wonderful if the designer puts their absolute best into making it a website that I would really appreciate. The website needs to show professionalism and also needs to make our web surfers find the information they need in a click. the company's colour is black and silver, and if those two colours could be integrated into the website it would be absolutely lovely. Please do contact me for any information.

Sincerely,
Dorian Vaskel

Industry/Entity Type

Security

```html
<!DOCTYPE html>
<html lang="en">
<head>
<meta charset="utf-8">
<title>Tavron Security Services Ltd</title>
<link rel="stylesheet" href="https://fonts.googleapis.com/css2?family=Oswald:wght@300;400&family=Arimo:wght@400;700&display=swap">
<style>
:root{
  --ink:#1c1c1c;
  --text:#555;
  --muted:#8a8a8a;
  --silver:#c9c9c9;
  --light:#efefef;
  --line:#d2d2d2;
  --white:#fff;
  --dark:#2b2b2b;
  --dark2:#3c3c3c;
  --field:#6a6a6a;
}
*{margin:0;padding:0;box-sizing:border-box}
html,body{width:1200px;height:2752px;overflow:hidden}
body{position:relative;background:var(--white);font-family:"Arimo",Arial,sans-serif;color:var(--text)}
.abs{position:absolute}
.cond{font-family:"Oswald","Arial Narrow",sans-serif;font-weight:400}

/* header */
.site-header{left:0;top:0;width:1200px;height:157px;background:linear-gradient(#fafafa,#e6e6e6);border-bottom:1px solid #cfcfcf}
.brand{left:157px;top:40px;display:flex;align-items:center;gap:12px}
.brand-dot{width:34px;height:34px;border-radius:50%;background:var(--ink)}
.brand-name{font-family:"Oswald",sans-serif;font-weight:400;font-size:22px;line-height:24px;color:var(--ink);letter-spacing:1px}
.main-nav{left:415px;top:94px;display:flex;gap:34px}
.main-nav a{font-family:"Arimo",sans-serif;font-size:13px;color:#333;text-decoration:none;letter-spacing:.3px}
.social{display:flex;gap:10px}
.social span{width:30px;height:30px;border-radius:50%;background:#b9b9b9;display:block}
.social.top{left:932px;top:29px}

/* hero */
.hero{left:0;top:157px;width:1200px;height:516px;background:radial-gradient(ellipse at 45% 30%,#5e5e5e 0%,#3b3b3b 55%,#262626 100%)}
.hero-photo{left:690px;top:157px;width:280px;height:516px;background:linear-gradient(90deg,rgba(200,200,200,0) 0%,rgba(190,190,190,.35) 35%,rgba(215,215,215,.55) 55%,rgba(120,120,120,.2) 100%)}
.hero-title{left:216px;top:380px;width:480px;font-family:"Oswald",sans-serif;font-weight:300;font-size:30px;line-height:42px;color:#f2f2f2}
.hero-title b{font-weight:400;font-size:36px}
.arrow{width:50px;height:50px;border-radius:50%;background:rgba(120,120,120,.7);display:flex;align-items:center;justify-content:center}
.arrow.small{width:34px;height:34px;background:#b5b5b5}

/* solutions */
.solutions{left:0;top:673px;width:1200px;height:710px;background:linear-gradient(#f5f5f5,#e4e4e4)}
.section-title{width:1200px;left:0;text-align:center;font-size:36px;color:var(--ink)}
.services-title{left:157px;top:826px;font-size:22px;color:var(--ink)}
.services-list{left:157px;top:880px;width:205px;list-style:none}
.services-list li{position:relative;padding-left:30px;font-size:12.5px;line-height:16px;color:#6b6b6b;margin-bottom:20px}
.services-list li::before{content:"";position:absolute;left:4px;top:2px;width:12px;height:12px;border-radius:50%;background:#d8d8d8}
.services-list li::after{content:"";position:absolute;left:8px;top:5px;width:3px;height:3px;border-right:1.5px solid #777;border-top:1.5px solid #777;transform:rotate(45deg)}
.custom-box{left:157px;top:1094px;width:211px;height:253px;background:linear-gradient(#8a8a8a,#c9c9c9 60%,#9d9d9d);border:1px solid #aaa;padding:20px 16px}
.custom-box p{font-family:"Oswald",sans-serif;color:#fff;font-size:18px;line-height:24px}
.custom-box .phone{font-size:24px;line-height:34px}
.custom-box .box-name{position:absolute;left:0;bottom:22px;width:100%;text-align:center;font-family:"Oswald",sans-serif;font-size:19px;color:var(--ink);letter-spacing:1px;line-height:22px}
.col-line{width:1px;background:#c6c6c6}
.row-line{height:1px;background:#c6c6c6}
.card{width:206px}
.card h3{display:flex;align-items:center;gap:8px;font-family:"Oswald",sans-serif;font-weight:400;font-size:16px;color:var(--ink)}
.card h3 svg{flex:none}
.card p{margin-top:14px;font-size:11.5px;line-height:15.5px;color:#777;letter-spacing:.2px}
.btn{display:inline-block;border:1px solid #bdbdbd;background:linear-gradient(#fff,#e3e3e3);font-size:11.5px;color:#333;padding:6px 10px;border-radius:2px}
.card .btn{position:absolute;right:0}

/* industries */
.industry{width:195px}
.industry .shot{width:195px;height:156px;border:4px solid #e4e4e4}
.industry h4{margin-top:16px;text-align:center;font-family:"Oswald",sans-serif;font-weight:400;font-size:17px;color:var(--ink)}

/* residential / commercial */
.split{left:0;top:1786px;width:1200px;height:482px;background:linear-gradient(#f7f7f7,#ececec)}
.divider{left:598px;top:1830px;width:2px;height:420px;background:linear-gradient(rgba(0,0,0,0),rgba(0,0,0,.12),rgba(0,0,0,0))}
.offer{width:380px;text-align:center}
.offer .ring{margin:0 auto;width:180px;height:180px;border-radius:50%;background:#dedede;padding:9px;box-shadow:0 4px 10px rgba(0,0,0,.15)}
.offer .ring div{width:162px;height:162px;border-radius:50%}
.offer h3{margin-top:20px;font-family:"Oswald",sans-serif;font-weight:400;font-size:18px;color:var(--ink)}
.offer p{margin-top:12px;font-size:12px;line-height:16px;color:#8d8d8d}
.offer .btn{margin-top:22px;padding:7px 22px}

/* footer */
.site-footer{left:0;top:2268px;width:1200px;height:484px;background:linear-gradient(#3f3f3f,#2a2a2a)}
.foot-h{font-family:"Oswald",sans-serif;font-weight:300;font-size:27px;color:#f0f0f0}
.foot-p{font-size:12px;line-height:15.5px;color:#9a9a9a}
.links{list-style:none}
.links li{position:relative;padding-left:22px;font-size:11.5px;color:#aaa;line-height:31.5px;letter-spacing:.3px}
.links li::before{content:"";position:absolute;left:2px;top:13px;width:5px;height:5px;border-right:1.5px solid #ddd;border-top:1.5px solid #ddd;transform:rotate(45deg)}
.field{width:274px;height:34px;background:var(--field);color:#e6e6e6;font-size:12px;padding:10px 20px;margin-bottom:12px}
.foot-bar{left:0;top:2658px;width:1200px;height:94px;background:#262626;border-top:1px solid #1a1a1a}
.copy{left:157px;top:2692px;font-size:12px;color:#9a9a9a}
.social.bottom{left:932px;top:2684px}
.social.bottom span{background:#8b8b8b}
</style>
</head>
<body>

<header class="abs site-header"></header>
<div class="abs brand">
  <span class="brand-dot"></span>
  <span class="brand-name">TAVRON<br><span style="font-size:13px;letter-spacing:.5px">Security Services Ltd.</span></span>
</div>
<nav class="abs main-nav">
  <a>HOME</a><a>ABOUT US</a><a>OUR SECURITY SOLUTIONS</a><a>INDUSTRIES WE SERVE</a><a>CONTACT US</a>
</nav>
<div class="abs social top"><span></span><span></span><span></span></div>

<section class="abs hero"></section>
<div class="abs hero-photo" role="img" aria-label="Security camera mounted on a steel pole"></div>
<h1 class="abs hero-title"><b>Lorem Ipsum</b> is simply dummy text of the printing and typesetting industry.</h1>
<div class="abs arrow" style="left:103px;top:388px"><svg width="16" height="22"><path d="M12 2 3 11l9 9" fill="none" stroke="#fff" stroke-width="2"/></svg></div>
<div class="abs arrow" style="left:1047px;top:388px"><svg width="16" height="22"><path d="M4 2l9 9-9 9" fill="none" stroke="#fff" stroke-width="2"/></svg></div>

<section class="abs solutions"></section>
<h2 class="abs section-title cond" style="top:722px">Our Security Solutions</h2>
<h3 class="abs services-title cond">Services</h3>
<ul class="abs services-list">
  <li>Property guards</li>
  <li>Corporate events security</li>
  <li>Personal bodyguard for high net worth individuals</li>
  <li>Security consultancy</li>
  <li>Private investigation</li>
</ul>
<div class="abs custom-box">
  <p>CUSTOM OPTIONS<br>AVAILABLE</p>
  <p class="phone">CALL 123-555-789</p>
  <div class="box-name">TAVRON<br>SECURITY SERVICES LTD.</div>
</div>

<div class="abs col-line" style="left:376px;top:822px;height:561px"></div>
<div class="abs col-line" style="left:598px;top:822px;height:561px"></div>
<div class="abs col-line" style="left:822px;top:822px;height:561px"></div>
<div class="abs col-line" style="left:1043px;top:822px;height:561px"></div>
<div class="abs row-line" style="left:376px;top:1072px;width:222px"></div>
<div class="abs row-line" style="left:598px;top:1092px;width:224px"></div>
<div class="abs row-line" style="left:822px;top:1056px;width:221px"></div>

<article class="abs card" style="left:390px;top:826px;height:236px">
  <h3><svg width="28" height="26"><path d="M2 13 14 2l12 11h-4v12H6V13z" fill="#111"/><rect x="11" y="16" width="6" height="9" fill="#fff"/></svg>Property Guards</h3>
  <p>Lorem ipsum dolor sit amet, cons ectetuer adipiscing elit, sed diam nonummy nibh euismod tincidunt<br><br>ut laoreet dolore magna aliquam erat volutpat. Ut wisi enim ad min im veniam, quis nostrud exerci ta tion ullamcorper suscipit lobortis nisl.</p>
  <span class="btn" style="top:203px">Read More</span>
</article>
<article class="abs card" style="left:612px;top:826px;height:250px">
  <h3><svg width="34" height="26"><circle cx="10" cy="6" r="5" fill="#111"/><circle cx="24" cy="6" r="5" fill="#111"/><path d="M2 25c0-8 3-12 8-12s8 4 8 12zM16 25c0-8 3-12 8-12s8 4 8 12z" fill="#111"/></svg>Personal Bodyguards</h3>
  <p>Duis autem vel eum iriure dolor i n hendrerit in vulputate velit esse molestie consequat.<br><br>Vel illum dolore eu feugiat nulla f acilisis at vero eros et accumsan et iusto odio dignissim qui blandi t praesent luptatum zzril delenit a ugue duis dolore te feugait nulla facilisi.</p>
  <span class="btn" style="top:222px">Read More</span>
</article>
<article class="abs card" style="left:838px;top:826px;height:220px">
  <h3><svg width="28" height="28"><circle cx="11" cy="11" r="8" fill="none" stroke="#111" stroke-width="3"/><path d="M17 17l9 9" stroke="#111" stroke-width="4"/></svg>Private Investigation</h3>
  <p>Ut wisi enim ad minim veniam, qu is nostrud exerci tation ullamcorp er suscipit lobortis nisl ut aliquip ex ea<br>commodo consequat. Duis autem vel eum iriure dolor in hen drerit in vulputate velit.</p>
  <span class="btn" style="top:186px">Read More</span>
</article>
<article class="abs card" style="left:390px;top:1090px">
  <h3><svg width="28" height="28"><circle cx="11" cy="7" r="6" fill="#111"/><path d="M2 27c0-9 4-13 9-13s9 4 9 13z" fill="#111"/><rect x="18" y="12" width="8" height="10" fill="#444"/></svg>Corporate Events Security</h3>
  <p>Lorem ipsum dolor sit amet, cons ectetuer adipiscing elit, sed diam nonummy nibh euismod tincidunt ut laoreet dolore magna aliquam erat volutpat. Ut wisi enim ad mini m veniam, quis nostrud exerci tati on ullamcorper suscipit lobortis n isl ut aliquip ex ea commodo cons equat.</p>
  <span class="btn" style="top:210px">Read More</span>
</article>
<article class="abs card" style="left:612px;top:1117px">
  <h3><svg width="32" height="24"><path d="M1 10l8-6 7 4 7-4 8 6-8 10-7-5-7 5z" fill="#111"/></svg>Security Consultancy</h3>
  <p>Duis autem vel eum iriure dolor in hendrerit in vulputate velit ess e molestie consequat, vel illum d olore eu feugiat nulla facilisis at vero eros et accumsan et iusto o dio dignissim qui blandit praese nt luptatum zzril delenit augue du is dolore</p>
  <span class="btn" style="top:201px">Read More</span>
</article>
<article class="abs card" style="left:838px;top:1074px">
  <h3><svg width="28" height="28"><circle cx="14" cy="14" r="12" fill="none" stroke="#111" stroke-width="2.5"/><circle cx="14" cy="11" r="4" fill="#111"/><path d="M7 22c1-5 4-6 7-6s6 1 7 6" fill="#111"/></svg>Executive Protection</h3>
  <p>Lorem ipsum dolor sit amet, cons ectetuer adipiscing elit, sed diam nonummy nibh euismod tincidunt ut laoreet dolore magna aliquam erat volutpat. Ut wisi enim ad mini m veniam, quis nostrud exerci tati on ullamcorper suscipit lobortis n isl ut aliquip ex ea commodo cons equat.</p>
  <span class="btn" style="top:200px">Read More</span>
</article>

<h2 class="abs section-title cond" style="top:1426px">Industries We Serve</h2>
<div class="abs arrow small" style="left:109px;top:1588px"><svg width="10" height="14"><path d="M8 1 2 7l6 6" fill="none" stroke="#fff" stroke-width="2"/></svg></div>
<div class="abs arrow small" style="left:1058px;top:1588px"><svg width="10" height="14"><path d="M2 1l6 6-6 6" fill="none" stroke="#fff" stroke-width="2"/></svg></div>
<div class="abs industry" style="left:157px;top:1530px">
  <div class="shot" role="img" aria-label="Flag flying outside a government building" style="background:linear-gradient(#6d93c9,#a9c3e6 45%,#33447a 60%,#8d8a80)"></div>
  <h4>Government</h4>
</div>
<div class="abs industry" style="left:391px;top:1530px">
  <div class="shot" role="img" aria-label="Solar panels and wind turbines under a blue sky" style="background:linear-gradient(#5f9fe0,#b7d6f4 45%,#2c5fa8 60%,#1d3f78)"></div>
  <h4>Energy and Environment</h4>
</div>
<div class="abs industry" style="left:620px;top:1530px">
  <div class="shot" role="img" aria-label="Oil pump jacks against an orange sunset" style="background:linear-gradient(#f6b43a,#e36a18 55%,#4a1d08 80%,#1a0a04)"></div>
  <h4>Oil and Gas</h4>
</div>
<div class="abs industry" style="left:848px;top:1530px">
  <div class="shot" role="img" aria-label="Cargo plane, truck and shipping freight" style="background:linear-gradient(#f4f4f4,#d6d6d6 55%,#9a9a9a 80%,#c79a5a)"></div>
  <h4>Transportation and Logistics</h4>
</div>

<section class="abs split"></section>
<div class="abs divider"></div>
<div class="abs offer" style="left:138px;top:1856px">
  <div class="ring"><div role="img" aria-label="Homeowner at the front door with a security keypad" style="background:linear-gradient(135deg,#e7d8c4,#b79a78 50%,#6e6a64)"></div></div>
  <h3>Residential Solutions</h3>
  <p>Lorem ipsum dolor sit amet, consectetur adipiscing elit. Sed in porta ut mauris vitae accumsan. Ut bibendum condim Phasellus placerat lectus nec odio fermentum, non Proin nec ligula condimentum, aliquet nisi id,</p>
  <span class="btn">Read More</span>
</div>
<div class="abs offer" style="left:679px;top:1856px">
  <div class="ring"><div role="img" aria-label="Security guard in uniform outside an office tower" style="background:linear-gradient(135deg,#7ea4d6,#3d5f92 45%,#151a22 75%)"></div></div>
  <h3>Commercial Solutions</h3>
  <p>Lorem ipsum dolor sit amet, consectetur adipiscing elit. Sed in porta ut mauris vitae accumsan. Ut bibendum condim Phasellus placerat lectus nec odio fermentum, non Proin nec ligula condimentum, aliquet nisi id,</p>
  <span class="btn">Read More</span>
</div>

<footer class="abs site-footer"></footer>
<h3 class="abs foot-h" style="left:157px;top:2318px">About us</h3>
<p class="abs foot-p" style="left:157px;top:2394px;width:310px">Lorem ipsum dolor sit amet, consectetur adipiscing elit. Morbi pellentesque iaculis justo eget fermentum. Pellentesque commodo iaculis neque, vitae tincidun odio pellentesque luctus. Aenean in eros eu magna vestibulum imperdiet pretium nec augue</p>
<p class="abs foot-p" style="left:157px;top:2483px;width:310px">Etiam quis turpis enim. Vestibulum auctor id mauris vulputate consequat. Suspendisse potenti. Cras at imperdiet elit. Integer fringilla tellus non diam condimentum, sed ultricies urna ultricies. Sed cong dui quis dui convallis dictum. Donec malesuada vulputate risus vitae vulputate. Maecenas in congue urna. Sed porttitor bibendum</p>
<h3 class="abs foot-h" style="left:541px;top:2318px">Quick Links</h3>
<ul class="abs links" style="left:536px;top:2386px">
  <li>HOME</li><li>OUR SERVICES</li><li>ABOUT</li><li>LOCATIONS</li><li>NEWS</li><li>CAREERS</li><li>CONTACT US</li>
</ul>
<h3 class="abs foot-h" style="left:767px;top:2318px">Newsletter Signup</h3>
<p class="abs foot-p" style="left:767px;top:2394px;width:280px">Fill the form below and recive our latest offers &amp; updates</p>
<div class="abs" style="left:767px;top:2460px">
  <div class="field">Your Name</div>
  <div class="field">Your Email</div>
  <span class="btn" style="margin-top:10px;padding:9px 32px;font-size:12px">Signup Now!</span>
</div>
<div class="abs foot-bar"></div>
<p class="abs copy">Copyright © 2014 Tavron Security Service LTD.</p>
<div class="abs social bottom"><span></span><span></span><span></span></div>

</body>
</html>
```